Business cards for a fun web development agency

Hi,I am building a web development agency. You can read about it on the website http://kite-loft.examplehost.com. Basically, I want to focus on free and open source products and stay as far away from the corporate business feeling as possible. I want to build a community so I want the business card to feel fun and approachable (at the risk of professional if need be). I am uploading some of my image assets in various file formats. Feel free to use them or make your own if you want just keeping in theme with the website.
Industry/Entity Type
Building
Contact Information for Business Card
Company Name: Boat ShedWebsite: www.kiteloftdev.example (it's currently in alpha on http://kite-loft.examplehost.com if you want to see the them we are trying to capture)My name is: Banner B. SchaferMy email: banner@boatsheddev.comMy phone: 0431 587 904
Look and feel

```html
<!DOCTYPE html>
<html lang="en">
<head>
<meta charset="utf-8">
<title>Kite Loft – Business Cards</title>
<link href="https://fonts.googleapis.com/css2?family=Open+Sans:wght@400;600;700&display=swap" rel="stylesheet">
<style>
  :root {
    --backdrop: #3a3a3c;
    --card: #ffffff;
    --navy: #1c3f73;
    --band-dark: #0f3a6e;
    --band-light: #1e7fd6;
    --text-muted: #4d5f78;
    --scene-sky: #9fd3d8;
    --scene-deep: #5aa3ad;
  }
  * { box-sizing: border-box; margin: 0; padding: 0; }
  html, body { width: 1200px; height: 852px; overflow: hidden; }
  body {
    background: var(--backdrop);
    font-family: "Open Sans", Arial, sans-serif;
    position: relative;
  }
  .card {
    position: absolute;
    width: 520px;
    height: 300px;
    background: var(--card);
    border-radius: 22px;
    overflow: hidden;
  }
  .card--front { left: 150px; top: 110px; }
  .card--back { left: 530px; top: 440px; }

  .wordmark {
    display: flex;
    align-items: center;
    gap: 14px;
    color: var(--navy);
    font-weight: 400;
    letter-spacing: 1px;
    text-transform: uppercase;
  }
  .wordmark__dot {
    border-radius: 50%;
    background: var(--navy);
    flex: none;
  }
  .card--front .wordmark {
    position: absolute;
    left: 0; right: 0; top: 118px;
    justify-content: center;
    font-size: 46px;
  }
  .card--front .wordmark__dot { width: 52px; height: 52px; }

  .back__band {
    position: absolute;
    left: 0; top: 0; bottom: 0;
    width: 46px;
    background: var(--band-dark);
    border-right: 7px solid var(--band-light);
  }
  .card--back .wordmark {
    position: absolute;
    left: 76px; top: 46px;
    font-size: 30px;
    gap: 10px;
  }
  .card--back .wordmark__dot { width: 36px; height: 36px; }

  .back__scene {
    position: absolute;
    right: 22px; top: 22px;
    width: 150px; height: 150px;
    border-radius: 50%;
    background: radial-gradient(circle at 45% 30%, var(--scene-sky), var(--scene-deep));
    box-shadow: 2px 3px 0 #e4eef0;
  }

  .person {
    position: absolute;
    left: 76px; top: 150px;
  }
  .person__name { font-size: 15px; font-weight: 700; color: var(--navy); }
  .person__title { font-size: 10px; color: var(--text-muted); margin-top: 1px; }

  .contacts {
    position: absolute;
    left: 76px; top: 206px;
    list-style: none;
  }
  .contacts li {
    display: flex;
    align-items: center;
    gap: 12px;
    font-size: 13px;
    color: var(--navy);
    line-height: 20px;
  }
  .contacts svg { width: 11px; height: 11px; fill: var(--navy); flex: none; }
</style>
</head>
<body>

<section class="card card--front">
  <div class="wordmark"><span>Kite</span><span class="wordmark__dot"></span><span>Loft</span></div>
</section>

<section class="card card--back">
  <div class="back__band"></div>
  <div class="wordmark"><span>Kite</span><span class="wordmark__dot"></span><span>Loft</span></div>
  <div class="back__scene" role="img" aria-label="Illustration of a blue shed at the end of a jetty over calm water"></div>

  <div class="person">
    <div class="person__name">Corwin T. Aldous</div>
    <div class="person__title">Managing Director</div>
  </div>

  <ul class="contacts">
    <li>
      <svg viewBox="0 0 12 12"><path d="M2.2 0.8l2 2-1 1.4c.6 1.6 1.9 2.9 3.5 3.5l1.4-1 2 2-1.4 2.2C5 10.6 1.4 7 0.8 2.2z"/></svg>
      <span>0431 587 904</span>
    </li>
    <li>
      <svg viewBox="0 0 12 12"><path d="M0 2h12v8H0z M0.8 2.6L6 6.6l5.2-4" fill="none" stroke="currentColor"/><path d="M0 2h12v8H0zM1 3v6h10V3L6 7z"/></svg>
      <span>corwin@kiteloftdev.example</span>
    </li>
    <li>
      <svg viewBox="0 0 12 12"><circle cx="6" cy="6" r="5.5"/><path d="M0.5 6h11M6 0.5c-2.5 3-2.5 8 0 11M6 0.5c2.5 3 2.5 8 0 11" stroke="#fff" stroke-width="0.8" fill="none"/></svg>
      <span>www.kiteloftdev.example</span>
    </li>
  </ul>
</section>

</body>
</html>
```